Bramwell Crest Electric van design

Looking to design a wrap for a 2021 varenta cargolux high roof using orange black and dark grey colors like in the logo

```html
<!DOCTYPE html>
<html lang="en">
<head>
<meta charset="utf-8">
<title>Bramwell Crest Electric — Van Wrap</title>
<link rel="stylesheet" href="https://fonts.googleapis.com/css2?family=Montserrat:wght@500&display=swap">
<style>
  :root {
    --backdrop: #ececec;
    --wrap-red: #e4493b;
    --wrap-red-deep: #c9362b;
    --wrap-black: #1c1c1c;
    --trim-grey: #2b2b2b;
    --pinline-grey: #4a4a4a;
    --glass: #8e9a9c;
    --rim: #b9bcbe;
    --white: #f7f7f7;
  }
  html, body {
    margin: 0;
    width: 1200px;
    height: 800px;
    overflow: hidden;
    background: var(--backdrop);
  }
  .van-wrap {
    display: block;
    width: 1200px;
    height: 800px;
  }
  .body-fill { fill: var(--wrap-red); }
  .body-lower { fill: var(--wrap-red-deep); }
  .rear-panel { fill: var(--wrap-black); }
  .sweep-pinline { fill: none; stroke: var(--pinline-grey); stroke-width: 10; }
  .skirt { fill: var(--trim-grey); }
  .cab-window { fill: var(--glass); stroke: var(--wrap-black); stroke-width: 4; }
  .panel-line { fill: none; stroke: rgba(0,0,0,0.25); stroke-width: 1.5; }
  .handle { stroke: var(--wrap-black); stroke-width: 4; stroke-linecap: round; }
  .tyre { fill: var(--wrap-black); }
  .rim { fill: var(--rim); }
  .hub { fill: #555; }
  .tail-light { fill: #c4202a; }
  .tail-lens { fill: #dddddd; }
  .brand-disc { fill: var(--white); stroke: var(--wrap-red); stroke-width: 2; }
  .brand-name {
    font-family: "Montserrat", sans-serif;
    font-weight: 500;
    font-size: 28px;
    fill: var(--white);
    letter-spacing: 1px;
  }
</style>
</head>
<body>
<svg class="van-wrap" viewBox="0 0 1200 800" xmlns="http://www.w3.org/2000/svg" role="img" aria-label="Bramwell Crest Electric van wrap, side view">
  <defs>
    <clipPath id="van-body">
      <path d="M150 240 Q150 222 175 222 L690 222 Q760 224 830 292 L920 400 Q1040 430 1055 450 L1062 575 L150 580 Z"/>
    </clipPath>
  </defs>

  <g clip-path="url(#van-body)">
    <rect class="body-fill" x="140" y="215" width="940" height="380"/>
    <rect class="body-lower" x="140" y="548" width="940" height="50"/>
    <path class="rear-panel" d="M140 215 L300 215 Q250 380 318 600 L140 600 Z"/>
    <path class="sweep-pinline" d="M322 215 Q272 380 340 600"/>
    <rect class="skirt" x="140" y="515" width="940" height="33"/>
    <polygon class="skirt" points="985,500 1070,500 1070,595 990,595"/>
  </g>

  <path class="panel-line" d="M170 288 L700 288 M710 290 L710 555 M202 300 L680 296 Q685 297 685 305 L680 410 L184 412 Z"/>
  <polygon class="cab-window" points="726,300 810,305 868,365 868,420 735,410 722,395"/>
  <line class="handle" x1="656" y1="438" x2="690" y2="438"/>
  <line class="handle" x1="726" y1="438" x2="760" y2="438"/>
  <rect class="tail-light" x="136" y="420" width="22" height="92" rx="2"/>
  <rect class="tail-lens" x="136" y="448" width="22" height="12"/>

  <circle class="tyre" cx="330" cy="575" r="56"/>
  <circle class="rim" cx="330" cy="575" r="37"/>
  <circle class="hub" cx="330" cy="575" r="12"/>
  <circle class="tyre" cx="928" cy="575" r="56"/>
  <circle class="rim" cx="928" cy="575" r="37"/>
  <circle class="hub" cx="928" cy="575" r="12"/>

  <circle class="brand-disc" cx="257" cy="352" r="49"/>
  <text class="brand-name" x="325" y="352">BRAMWELL CREST</text>
  <text class="brand-name" x="325" y="388">ELECTRIC</text>
</svg>
</body>
</html>
```